FunBrixo Business Card

We need a business card design for our company. We sell construction-themed amusement rides for kids.

Contact Information for Business Card

Contact info on business card should include:
Carl Dunning
Co-Founder & COO
(833) 571-FUNBRIX
Carl@funbrixo-demo.com
www.funbrixo-demo.com

```html
<!DOCTYPE html>
<html lang="en">
<head>
<meta charset="utf-8">
<title>FunBrixo Business Card</title>
<link href="https://fonts.googleapis.com/css2?family=Arimo:wght@400;700&display=swap" rel="stylesheet">
<style>
  :root {
    --backdrop: #0b0b0c;
    --card: #2a2a2c;
    --card-edge: #e8531f;
    --orange: #ef5a24;
    --blue: #2a9fd8;
    --grey: #b9b9bb;
    --rule: #6d6d70;
  }
  * { box-sizing: border-box; margin: 0; padding: 0; }
  html, body {
    width: 1200px;
    height: 822px;
    overflow: hidden;
    background: var(--backdrop);
    font-family: "Arimo", Arial, sans-serif;
  }
  .stage {
    position: relative;
    width: 1200px;
    height: 822px;
    display: flex;
    align-items: center;
    justify-content: center;
    gap: 60px;
  }
  .card {
    width: 500px;
    height: 286px;
    background: var(--card);
    border: 2px solid var(--card-edge);
    border-radius: 3px;
    position: relative;
    display: flex;
    flex-direction: column;
    align-items: center;
  }
  .brand {
    display: flex;
    align-items: center;
    gap: 10px;
    color: var(--orange);
    font-weight: 700;
    letter-spacing: 0.5px;
  }
  .brand-dot {
    border-radius: 50%;
    background: var(--orange);
  }
  .card--front .brand { margin-top: 58px; font-size: 44px; }
  .card--front .brand-dot { width: 16px; height: 16px; }
  .card--back { justify-content: center; }
  .card--back .brand { font-size: 54px; }
  .card--back .brand-dot { width: 20px; height: 20px; }
  .person { margin-top: 26px; text-align: center; }
  .person-name {
    color: var(--orange);
    font-weight: 700;
    font-size: 17px;
    text-transform: uppercase;
  }
  .person-role {
    color: var(--grey);
    font-size: 14px;
    margin-top: 2px;
  }
  .divider {
    width: 150px;
    height: 1px;
    background: var(--rule);
    margin: 10px 0 9px;
  }
  .contact {
    color: var(--grey);
    font-size: 14px;
    text-align: center;
    line-height: 1.45;
  }
  .label { color: var(--orange); font-weight: 700; }
  .web-accent { color: var(--orange); }
  .web-name { color: var(--blue); }
</style>
</head>
<body>
<main class="stage">
  <section class="card card--front" aria-label="Business card front">
    <div class="brand"><span class="brand-dot"></span><span>FunBrixo</span></div>
    <div class="person">
      <p class="person-name">Carl Dunning</p>
      <p class="person-role">Co-Founder &amp; COO</p>
    </div>
    <div class="divider"></div>
    <div class="contact">
      <p><span class="label">P:</span> (833) 571-FUNBRIX | <span class="label">E:</span> Carl@funbrixo-demo.com</p>
      <p><span class="web-accent">www.</span><span class="web-name">funbrixo-demo</span><span class="web-accent">.com</span></p>
    </div>
  </section>
  <section class="card card--back" aria-label="Business card back">
    <div class="brand"><span class="brand-dot"></span><span>FunBrixo</span></div>
  </section>
</main>
</body>
</html>
```